Yacht, Boats, Watersports company needs a redesign of business card

Hello Designers!
We are a Boat dealership company that sells fun in the water, we sell boats, Yachts, Kayaks and also yacht WaterSport toys. We are looking to redesign our business cards in to something a little bit more sophisticated. in a way that we can make better use of our company colors. I'm attaching a zipped file containing the company 3 sets of company logo which one is an horizontal another one is a vertical and also a chromed 3d logo. Also is included two set of business cards that we use and also some designs that i think it's interesting. We use PMS 2026c Orange and PMS 7687C Blue. I would like to see at least two different options with the orange as accent and also using blue as an accent color. It's really important for the business cards to have a font option and size that is legible to most people. Our current website is wwww.coralpennant.com. Please visit if you want to have a better feeling of the Boat dealership
You can send Single sided or double side options. We are now using single sided but we may be open for a double side option if we really like the design.
Target Market(s)
Marine, boat sales, yacht sales, water toys sales/
Contact Information for Business Card
Name: Dale Whitcombe
Address: 212 North Fenwick Lane,
Coral Reach, FL 33187
Phone: 954-731-8842
Fax: 954:731-8843
Cell: 954-382-1490
Email: dw@coralpennant.com
Website: coralpennant.com
Requirements
Must have
- the current information of the business card provided.
logo
use the PMS Colors
Nice to have
- a touch of elegance and sophistication but simple
Should not have
- should not have any typography that is hard to read, the card should be simple but yet sophisticated.

```html
<!DOCTYPE html>
<html lang="en">
<head>
<meta charset="utf-8">
<title>Coral Pennant — Business Card</title>
<link href="https://fonts.googleapis.com/css2?family=Roboto:wght@400;500&family=Roboto+Condensed:wght@700&display=swap" rel="stylesheet">
<style>
  :root {
    --navy: #10457a;
    --orange: #e95e2f;
    --white: #ffffff;
    --disc: #f4f4f4;
    --backdrop: #e4e4e4;
  }
  * { margin: 0; padding: 0; box-sizing: border-box; }
  html, body { width: 1200px; height: 960px; overflow: hidden; }
  body { background: var(--backdrop); position: relative; font-family: "Roboto", Arial, sans-serif; }

  .card { position: absolute; left: 309px; width: 588px; height: 335px; overflow: hidden; }

  /* front */
  .card-front { top: 118px; background: var(--navy); }
  .front-dot {
    position: absolute; left: 244px; top: 95px; width: 100px; height: 100px;
    border-radius: 50%; border: 6px solid var(--white);
  }
  .front-wordmark {
    position: absolute; left: 0; right: 0; top: 210px;
    text-align: center; color: var(--white);
    font-weight: 500; font-size: 32px; line-height: 40px;
    letter-spacing: 10px; padding-left: 10px; text-transform: uppercase;
  }

  /* back */
  .card-back { top: 505px; background: var(--orange); }
  .back-panel {
    position: absolute; left: 429px; top: 0; width: 159px; height: 100%;
    background: var(--navy); border-left: 5px solid var(--white);
  }
  .name-marker {
    position: absolute; left: 0; top: 58px; width: 0; height: 0;
    border-top: 27px solid transparent; border-bottom: 27px solid transparent;
    border-left: 37px solid var(--white);
  }
  .holder-name {
    position: absolute; left: 50px; top: 67px;
    font-family: "Roboto Condensed", "Arial Narrow", sans-serif; font-weight: 700; font-size: 27px;
    color: var(--white);
  }
  .holder-name .first { color: var(--navy); }
  .address { position: absolute; left: 50px; top: 149px; color: var(--white); font-size: 16px; line-height: 20px; }
  .contacts { position: absolute; left: 50px; top: 198px; list-style: none; color: var(--white); font-size: 16px; line-height: 19.8px; }
  .contacts li { display: flex; align-items: center; gap: 5px; }
  .contacts svg { width: 13px; height: 13px; fill: var(--navy); flex: none; }

  .brand-disc {
    position: absolute; left: 337px; top: 72px; width: 190px; height: 190px; border-radius: 50%;
    background: var(--disc); border: 10px solid var(--white);
    display: flex; align-items: center; justify-content: center;
    color: var(--navy); font-weight: 500; font-size: 17px; letter-spacing: 1px; text-transform: uppercase;
  }
</style>
</head>
<body>

<section class="card card-front">
  <div class="front-dot"></div>
  <div class="front-wordmark">Coral Pennant</div>
</section>

<section class="card card-back">
  <div class="back-panel"></div>
  <div class="name-marker"></div>
  <h1 class="holder-name"><span class="first">Dale</span> Whitcombe</h1>
  <p class="address">212 North Fenwick Lane,<br>Coral Reach, FL 33187</p>
  <ul class="contacts">
    <li><svg viewBox="0 0 16 16"><path d="M3.5 1l3 3-1.8 1.8a9 9 0 0 0 5.5 5.5L12 9.5l3 3-2 2C7 14 2 9 1.5 3z"/></svg>954-731-8842</li>
    <li><svg viewBox="0 0 16 16"><path d="M4 1h8v4H4zM1 6h14v6h-3v3H4v-3H1zM5 10v4h6v-4z"/></svg>954:731-8843</li>
    <li><svg viewBox="0 0 16 16"><path d="M4 0h8v16H4zM5.5 2v10h5V2z"/></svg>954-382-1490</li>
    <li><svg viewBox="0 0 16 16"><path d="M1 3h14v10H1zm1.5 1.5v.3L8 9l5.5-4.2v-.3zm0 2.2v4.8h11V6.7L8 10.9z"/></svg>dw@coralpennant.com</li>
    <li><svg viewBox="0 0 16 16"><path d="M8 1a7 7 0 1 0 0 14A7 7 0 0 0 8 1zm0 1.4c.8 1 1.4 2.4 1.6 4.1H6.4C6.6 4.8 7.2 3.4 8 2.4zM2.5 7.5h2.4c0 1.1.2 2.1.6 3H3.3a5.6 5.6 0 0 1-.8-3zm4 0h3c0 1.1-.2 2.1-.6 3H7.1c-.4-.9-.6-1.9-.6-3zm4.6 0h2.4a5.6 5.6 0 0 1-.8 3h-2.2c.4-.9.6-1.9.6-3zM3.3 5.5a5.6 5.6 0 0 1 2.6-2.6c-.5.8-.9 1.7-1 2.6zm7.8 0c-.1-.9-.5-1.8-1-2.6a5.6 5.6 0 0 1 2.6 2.6zM7.1 12h1.8L8 13.6zm-3 0h1.5l.4 1.1A5.6 5.6 0 0 1 4.1 12zm6.3 0h1.5a5.6 5.6 0 0 1-1.9 1.1z"/></svg>coralpennant.com</li>
  </ul>
  <div class="brand-disc">Coral Pennant</div>
</section>

</body>
</html>
```